Bramwell IT Services Business Card

Bramwell IT Services are a Perth based IT Services company. We would like to incorporate our company logo (attached) and stick with the blue that is in that design. I would like a clean look design that isn't too busy, yet creates a lasting image that is instantly recognisable in the recipients mind.

Target Market(s)

The target audience is small/medium business owners.

Industry/Entity Type

Business

Font styles to use
Serif
Sans Serif

Colors

Designer to choose colors to be used in the design.

Requirements
Must have
• The design should include:
Business name: Bramwell IT Services
Directors Name: Marcus Tenley
Phone Number: 0483 562 904
Email: support@bramwellit.com.au
Website: www.bramwellit.com.au

```html
<!DOCTYPE html>
<html lang="en">
<head>
<meta charset="utf-8">
<title>Bramwell IT Services – Business Card</title>
<link rel="stylesheet" href="https://fonts.googleapis.com/css2?family=Arimo:wght@400;700&display=swap">
<style>
  :root {
    --page-bg: #d9d9d9;
    --card-white: #ffffff;
    --band-dark: #0c3a63;
    --band-light: #1f6aa3;
    --band-rule: #e9eef3;
    --brand-blue: #2563b8;
    --text-dark: #333a40;
    --icon-blue: #1d4f8a;
  }
  * { margin: 0; padding: 0; box-sizing: border-box; }
  html, body {
    width: 1200px; height: 900px; overflow: hidden;
    background: var(--page-bg);
    font-family: "Arimo", Arial, sans-serif;
  }
  .canvas {
    position: relative; width: 1200px; height: 900px;
  }
  .card {
    position: absolute; left: 300px;
    width: 600px; height: 367px;
    background: var(--card-white);
    box-shadow: 0 6px 18px rgba(0,0,0,0.18);
    overflow: hidden;
  }
  .card--front { top: 60px; }
  .card--back { top: 473px; }

  /* front */
  .front-band {
    position: absolute; left: 0; top: 0; width: 100%; height: 200px;
    background: linear-gradient(100deg, var(--band-dark) 0%, #155087 55%, var(--band-light) 100%);
    border-bottom: 6px solid var(--band-rule);
  }
  .brand-name {
    color: var(--brand-blue);
    font-weight: 700;
    letter-spacing: 0.5px;
    white-space: nowrap;
    display: flex; align-items: center; gap: 10px;
  }
  .brand-square {
    width: 16px; height: 16px; background: var(--brand-blue);
  }
  .front-band .brand-name {
    position: absolute; left: 40px; top: 88px;
    font-size: 26px; color: #ffffff;
  }
  .front-band .brand-square { background: #ffffff; }
  .holder {
    position: absolute; right: 34px; top: 216px; text-align: right;
  }
  .holder__name {
    color: var(--brand-blue); font-size: 21px; font-weight: 700;
  }
  .holder__role {
    color: var(--text-dark); font-size: 13px; margin-top: 2px;
  }
  .contacts {
    position: absolute; left: 40px; bottom: 30px;
    list-style: none; font-size: 14.5px; color: var(--text-dark);
  }
  .contacts li {
    display: flex; align-items: center; gap: 10px; line-height: 22px;
  }
  .contacts svg { width: 14px; height: 14px; flex: none; }

  /* back */
  .back-layout {
    position: absolute; left: 0; top: 0; width: 100%; height: 100%;
    display: flex; align-items: center; justify-content: center; gap: 40px;
  }
  .card--back .brand-name { font-size: 27px; }
  .back-web {
    color: var(--brand-blue); font-size: 17px; font-weight: 700;
  }
</style>
</head>
<body>
<div class="canvas">

  <section class="card card--front" aria-label="Business card front">
    <div class="front-band">
      <div class="brand-name"><span class="brand-square"></span>Bramwell IT Services</div>
    </div>
    <div class="holder">
      <div class="holder__name">Marcus Tenley</div>
      <div class="holder__role">Director</div>
    </div>
    <ul class="contacts">
      <li>
        <svg viewBox="0 0 16 16" aria-hidden="true"><circle cx="8" cy="8" r="8" fill="var(--icon-blue)"/><path d="M5 4.5h2l.7 2-1.1.8a5 5 0 0 0 2.1 2.1l.8-1.1 2 .7v2c0 .5-.4.8-.9.8A6.6 6.6 0 0 1 4.2 5.4c0-.5.3-.9.8-.9z" fill="#fff"/></svg>
        0483 562 904
      </li>
      <li>
        <svg viewBox="0 0 16 16" aria-hidden="true"><circle cx="8" cy="8" r="8" fill="var(--icon-blue)"/><rect x="4" y="5" width="8" height="6" fill="#fff"/><path d="M4 5l4 3.3L12 5" stroke="var(--icon-blue)" stroke-width="1" fill="none"/></svg>
        support@bramwellit.com.au
      </li>
      <li>
        <svg viewBox="0 0 16 16" aria-hidden="true"><circle cx="8" cy="8" r="8" fill="var(--icon-blue)"/><circle cx="8" cy="8" r="4.5" stroke="#fff" stroke-width="1" fill="none"/><ellipse cx="8" cy="8" rx="2" ry="4.5" stroke="#fff" stroke-width="1" fill="none"/><path d="M3.5 8h9" stroke="#fff" stroke-width="1"/></svg>
        www.bramwellit.com.au
      </li>
    </ul>
  </section>

  <section class="card card--back" aria-label="Business card back">
    <div class="back-layout">
      <div class="brand-name"><span class="brand-square"></span>Bramwell IT Services</div>
      <div class="back-web">www.bramwellit.com.au</div>
    </div>
  </section>

</div>
</body>
</html>
```